Brovanek Data Yellow rose letterhead

I have a new logo for my company but in its current form it is too large to be used on letterhead or as a email signature. I need to have the designer use elements from the current logo and create something close to the original but more suited for smaller items.
Updates

I just uploaded a copy of our logo that does not have the weathered affect. Thanks

Reason: More time for revisions

Industry/Entity Type

It Company

Requirements
Must have
• The design must maintain the visual effect of the current logo. It needs to include the yellow rose and the name of the company.
Nice to have
• It would be nice to maintain the stamp theme and incorporate my name, address, phone, email. etc.

```html
<!DOCTYPE html>
<html lang="en">
<head>
<meta charset="utf-8">
<title>Brovanek Data Letterhead</title>
<link href="https://fonts.googleapis.com/css2?family=Arimo:wght@400;700&family=Cinzel:wght@700&display=swap" rel="stylesheet">
<style>
  :root {
    --backdrop: #c4c4c4;
    --paper: #ffffff;
    --bark: #5b4a42;
    --teal: #3cb4b6;
    --gold: #f2b441;
    --rose: #f7c92f;
    --rose-faint: #fdf0c4;
    --ink-light: #ffffff;
  }
  * { margin: 0; padding: 0; box-sizing: border-box; }
  html, body {
    width: 848px; height: 1200px; overflow: hidden;
    background: var(--backdrop);
  }
  .letterhead {
    position: absolute; left: 108px; top: 152px;
    width: 635px; height: 898px;
    background: var(--paper);
    overflow: hidden;
    font-family: "Arimo", Arial, sans-serif;
  }
  .header-band {
    position: absolute; left: 0; top: 0; width: 100%; height: 76px;
    background: var(--bark);
  }
  .rule { position: absolute; left: 0; width: 100%; }
  .rule--gold-top { top: 77px; height: 2px; background: var(--gold); }
  .rule--teal-top { top: 81px; height: 3px; background: var(--teal); }
  .rule--gold-bottom { top: 822px; height: 4px; background: var(--gold); }
  .rule--teal-bottom { top: 831px; height: 4px; background: var(--teal); }
  .brand-mark {
    position: absolute; left: 15px; top: 16px;
    width: 106px; height: 106px; border-radius: 50%;
    background: var(--rose);
  }
  .brand-name {
    position: absolute; left: 172px; top: 14px;
    width: 292px; text-align: center;
    font-family: "Cinzel", Georgia, serif; font-weight: 700;
    font-size: 30px; line-height: 34px;
    color: var(--teal); white-space: nowrap;
  }
  .brand-tagline {
    position: absolute; left: 172px; top: 51px;
    width: 292px; text-align: center;
    font-size: 13px; letter-spacing: 3.4px;
    color: var(--ink-light); white-space: nowrap;
  }
  .rose-watermark {
    position: absolute; left: -40px; top: 460px;
    width: 400px; height: 380px; border-radius: 48% 52% 40% 45%;
    background: radial-gradient(ellipse at 45% 50%, #fde9a8 0%, var(--rose-faint) 55%, rgba(253,240,196,0) 75%);
  }
  .footer-band {
    position: absolute; left: 0; top: 841px; width: 100%; height: 57px;
    background: var(--bark); color: var(--ink-light);
  }
  .address { position: absolute; left: 36px; top: 9px; font-size: 12.5px; }
  .contact { position: absolute; top: 29px; display: flex; align-items: center; font-size: 12.5px; }
  .contact--email { left: 36px; }
  .contact--phone { left: 240px; }
  .contact svg { margin-right: 16px; }
  .signatory {
    position: absolute; right: 14px; top: 12px;
    font-size: 12px; font-weight: 700;
  }
</style>
</head>
<body>
  <main class="letterhead">
    <div class="rose-watermark" role="img" aria-label="Faint yellow rose watermark"></div>
    <header class="header-band">
      <div class="brand-name">Brovanek Data</div>
      <div class="brand-tagline">SMART DATA SOLUTIONS</div>
    </header>
    <div class="rule rule--gold-top"></div>
    <div class="rule rule--teal-top"></div>
    <div class="brand-mark" aria-hidden="true"></div>

    <div class="rule rule--gold-bottom"></div>
    <div class="rule rule--teal-bottom"></div>
    <footer class="footer-band">
      <div class="address">418 Cedar Hollow Road, Ste 210, Marble Falls, TX 78654</div>
      <div class="contact contact--email">
        <svg width="19" height="13" viewBox="0 0 19 13" aria-hidden="true">
          <rect x="0.5" y="0.5" width="18" height="12" fill="none" stroke="#fff"/>
          <path d="M0.5 0.5 L9.5 7 L18.5 0.5 M0.5 12.5 L7 5.5 M18.5 12.5 L12 5.5" fill="none" stroke="#fff"/>
        </svg>
        <span>nora@brovanek-data.com</span>
      </div>
      <div class="contact contact--phone">
        <svg width="18" height="13" viewBox="0 0 18 13" aria-hidden="true">
          <path d="M1 4 Q9 -1 17 4 L15 6 L12 5 L12 3.5 Q9 2.5 6 3.5 L6 5 L3 6 Z" fill="#fff"/>
          <path d="M4 7 L14 7 L16 12 L2 12 Z" fill="#fff"/>
          <circle cx="9" cy="9.3" r="1.6" fill="#5b4a42"/>
        </svg>
        <span>1-800-555-0147</span>
      </div>
      <div class="signatory">Nora Whitlock, PhD</div>
    </footer>
  </main>
</body>
</html>
```